Social Media App Needs PPT Template

We need a PowerPoint template for a new social media company based in the DC area called "Bold Ledger." We provide an interactive digital platform for executives to share actionable advice. We would like to see designs that use our orange logo color as an accent, but are mainly grey, white, and black. The final design should communicate clean, chic, modern, and professional.

Target Market(s)

Executives

Industry/Entity Type

Information Technology

Font styles to use
Sans Serif

Colors
f78f20
fbe7d2
ffffff
000000
e8e8e8
757575

Requirements
Must have
• My project must have title page and many options for the body of the ppt (graphs, tables, etc). It also needs to be easy to modify. I must have someone who is experienced in creating powerpoint templates.
Nice to have
• It would be nice to have a very modern and clean design that includes the logo on every page, but still leaves a lot of room for the content of the slide
Should not have
• My design project should not look to busy.

```html
<!DOCTYPE html>
<html lang="en">
<head>
<meta charset="utf-8">
<title>Bold Ledger – Presentation Template</title>
<link href="https://fonts.googleapis.com/css2?family=Lato:wght@300;400;700&family=Oswald:wght@400&display=swap" rel="stylesheet">
<style>
:root{
  --stage:#4e4e4e;
  --stage-line:#5a5a5a;
  --label:#c4c4c4;
  --navy:#262b35;
  --orange:#f78f20;
  --peach:#fbe7d2;
  --white:#ffffff;
  --black:#000000;
  --light:#e8e8e8;
  --mid:#757575;
  --grey-box:#5d5d5d;
  --dark-box:#222222;
  --text:#8a8a8a;
}
*{box-sizing:border-box;margin:0;padding:0}
html,body{width:1200px;height:722px;overflow:hidden;background:var(--stage)}
.canvas{position:relative;width:1200px;height:722px;background:var(--stage);font-family:'Lato',sans-serif;overflow:hidden}
.grid-line{position:absolute;background:var(--stage-line)}
.page-label{position:absolute;width:248px;text-align:center;font-size:7px;color:var(--label);font-family:'Lato',sans-serif}
.slide{position:absolute;width:248px;height:185px;background:var(--white);overflow:hidden}
.c1{left:30px}.c2{left:331px}.c3{left:630px}.c4{left:930px}
.r1{top:40px}.r2{top:281px}.r3{top:522px}
.l1{top:20px}.l2{top:261px}.l3{top:502px}

/* header */
.slide-header{position:absolute;left:0;top:0;width:248px;height:31px;border-top:3px solid var(--orange)}
.slide-header::after{content:"";position:absolute;left:0;top:1.5px;width:248px;height:26.5px;background:var(--navy)}
.slide-title{position:absolute;left:11px;top:9px;z-index:1;font-family:'Oswald',sans-serif;font-size:11.5px;color:var(--white);letter-spacing:-.1px;text-transform:uppercase}
.brand{position:absolute;right:11px;top:11px;z-index:1;display:flex;align-items:center;gap:3px}
.brand-dot{width:6px;height:6px;border-radius:50%;background:var(--orange)}
.brand-name{font-family:'Lato',sans-serif;font-weight:700;font-size:7.5px;color:var(--white);letter-spacing:.2px}

/* footer */
.slide-footer{position:absolute;right:10px;bottom:8px;width:72px;border-top:.5px solid #d6d6d6;padding-top:2.5px;text-align:right;font-size:3.2px;color:#9a9a9a}

.body-text{font-size:3.4px;line-height:1.45;color:var(--text);text-align:justify}
.accent-text{color:var(--orange);font-weight:700}
.img-fill{position:absolute}

/* page 1 */
.cover-photo{left:0;top:0;width:248px;height:165px;background:radial-gradient(ellipse at 70% 70%,#c87a14 0%,#7a4a0c 40%,#2a1a06 85%)}
.cover-brand{position:absolute;left:0;top:64px;width:248px;text-align:center;display:flex;justify-content:center;align-items:center;gap:5px}
.cover-brand .brand-name{font-size:14px;letter-spacing:.6px}
.cover-brand .brand-dot{width:9px;height:9px}
.cover-tagline{position:absolute;left:0;top:139px;width:248px;text-align:center;font-size:8.6px;font-weight:300;color:var(--white)}
.cover-rule{position:absolute;left:0;top:164px;width:248px;height:2px;background:var(--white)}
.cover-band{position:absolute;left:0;top:166px;width:248px;height:19px;background:var(--navy);text-align:center;font-size:4.5px;color:#c8c8c8;line-height:19px}

/* page 2 */
.transition-photo{left:0;top:0;width:248px;height:185px;background:radial-gradient(ellipse at 55% 40%,#6fc3ea 0%,#2377a8 35%,#0e3350 75%,#081c2c 100%)}
.transition-band{position:absolute;left:66px;top:146px;width:182px;height:30px}
.transition-title{position:absolute;left:130px;top:153px;font-size:13px;font-weight:300;color:var(--white)}

/* page 3 */
.about-left{position:absolute;left:11px;top:41px;width:112px}
.about-left p+p{margin-top:3px}
.about-right{position:absolute;left:131px;top:41px;width:107px}
.about-photo{left:131px;top:82px;width:107px;height:72px;background:linear-gradient(160deg,#5a5f66 0%,#2d3036 55%,#15171a 100%)}

/* page 4 */
.device-illustration{left:22px;top:52px;width:78px;height:54px;background:linear-gradient(180deg,#4aa9e0 0%,#2c6fa4 60%,#3a3f46 100%);border-radius:2px}
.about4-text{position:absolute;left:14px;top:113px;width:95px}
.bullet-list{position:absolute;left:132px;top:54px;width:110px;list-style:none}
.bullet-list li{position:relative;padding-left:8px;font-size:3.8px;line-height:1.4;color:#666;margin-bottom:9px}
.bullet-list li::before{content:"";position:absolute;left:0;top:1.5px;width:2.5px;height:2.5px;background:var(--orange)}

/* page 5 */
.feature{position:absolute;top:52px;width:66px;text-align:center}
.feature svg{display:block;margin:0 auto 10px}
.feature .body-text{text-align:justify;text-align-last:center}

/* chart pages */
.chart{position:absolute;left:8px;top:36px}
.chart-text{position:absolute;left:12px;top:133px;width:224px}

/* page 8 */
.donut{position:absolute;left:92px;top:67px}
.donut-note{position:absolute;width:62px}
.donut-note h4{font-size:5.6px;font-weight:700;color:#3a3f48;letter-spacing:.1px;border-bottom:.5px solid #cfcfcf;padding-bottom:1px;margin-bottom:2.5px}
.donut-note .body-text{text-align:left;font-size:3.4px}
.note-orange h4{color:var(--orange)}
.note-muted h4{color:#c2c2c2}
.note-muted .body-text{color:#b4b4b4}
.donut-link{position:absolute;height:.5px;background:#cfcfcf}

/* page 9 */
.data-table{position:absolute;left:13px;top:76px;width:225px;border-collapse:collapse;font-size:3.8px}
.data-table thead th{font-weight:400;color:#999;height:11px;border-top:.6px solid #cfcfcf;text-align:center}
.data-table td{height:18px;text-align:center;font-size:6.5px;color:#7a7a7a}
.data-table td.row-name{width:58px;text-align:left;padding-left:24px;font-size:3.8px}
.data-table tr.row-accent td{background:var(--orange);color:var(--white);border-top:2px solid var(--white);border-bottom:2px solid var(--white)}

/* page 10 */
.member{position:absolute;width:108px;height:36px}
.member-photo{position:absolute;left:0;top:0;width:31px;height:34px;background:linear-gradient(180deg,#d9d4ce 0%,#a9a39c 100%)}
.member-info{position:absolute;left:36px;top:0;width:72px}
.member-name{font-size:5px;font-weight:700;color:#333}
.member-role{font-size:3.4px;color:#999;margin-bottom:2px}
.member-info .body-text{font-size:3.2px;text-align:left}

/* page 11 */
.stat{position:absolute;width:106px;height:47px;color:var(--white)}
.stat svg{position:absolute;left:6px;top:13px}
.stat-value{position:absolute;left:35px;top:7px;font-size:9px;font-weight:400}
.stat-text{position:absolute;left:35px;top:20px;width:66px;font-size:3.4px;line-height:1.35}
.stat-orange{background:var(--orange)}
.stat-grey{background:var(--grey-box)}
.stat-navy{background:var(--navy)}
.stat-dark{background:var(--dark-box)}

/* page 12 */
.closing-top{position:absolute;left:0;top:0;width:248px;height:137px;background:var(--navy)}
.closing-brand{position:absolute;left:0;top:52px;width:248px;display:flex;justify-content:center;align-items:center;gap:4px}
.closing-brand .brand-name{font-size:10px;letter-spacing:.5px}
.closing-title{position:absolute;left:0;top:98px;width:248px;text-align:center;font-size:22px;font-weight:300;color:var(--white);letter-spacing:.8px}
.closing-url{position:absolute;left:0;top:168px;width:248px;text-align:center;font-size:5px;color:#999}
</style>
</head>
<body>
<div class="canvas">
  <div class="grid-line" style="left:299px;top:0;width:1px;height:722px"></div>
  <div class="grid-line" style="left:599px;top:240px;width:1px;height:482px"></div>
  <div class="grid-line" style="left:899px;top:0;width:1px;height:722px"></div>
  <div class="grid-line" style="left:0;top:240px;width:1200px;height:1px"></div>
  <div class="grid-line" style="left:0;top:481px;width:1200px;height:1px"></div>

  <!-- Page 1 -->
  <div class="page-label c1 l1">Page 1</div>
  <section class="slide c1 r1">
    <div class="img-fill cover-photo" role="img" aria-label="Close-up of hands typing on a glowing laptop keyboard"></div>
    <div class="cover-brand"><span class="brand-dot"></span><span class="brand-name">Bold Ledger</span></div>
    <p class="cover-tagline">interactive digital platform to share actionable advice</p>
    <div class="cover-rule"></div>
    <div class="cover-band">www.boldledger.com</div>
  </section>

  <!-- Page 2 -->
  <div class="page-label c2 l1">Page 2</div>
  <section class="slide c2 r1">
    <div class="img-fill transition-photo" role="img" aria-label="Hands holding a smartphone surrounded by floating app icons"></div>
    <svg class="transition-band" width="182" height="30" viewBox="0 0 182 30" aria-hidden="true">
      <polygon points="14,0 182,0 182,30 0,30" fill="#262b35" opacity=".85"/>
      <polygon points="14,0 22,0 8,30 0,30" fill="#f78f20"/>
    </svg>
    <p class="transition-title">Transition Page</p>
  </section>

  <!-- Page 3 -->
  <div class="page-label c3 l1">Page 3</div>
  <section class="slide c3 r1">
    <header class="slide-header"><h2 class="slide-title">About our company</h2><div class="brand"><span class="brand-dot"></span><span class="brand-name">Bold Ledger</span></div></header>
    <div class="about-left">
      <p class="body-text accent-text">Lorem ipsum dolor sit amet, consectetuer adipiscing elit, sed diam nonummy nibh euismod tincidunt ut laoreet dolore magna aliquam erat volutpat.</p>
      <p class="body-text">Duis autem vel eum iriure dolor in hendrerit in vulputate velit esse molestie consequat, vel illum dolore eu feugiat nulla facilisis at vero eros.</p>
      <p class="body-text">Duis autem vel eum iriure dolor in hendrerit in vulputate velit esse molestie consequat, vel illum dolore eu feugiat nulla facilisis at vero eros.</p>
    </div>
    <div class="about-right"><p class="body-text">Duis autem vel eum iriure dolor in hendrerit in vulputate velit esse molestie consequat, vel illum dolore eu feugiat nulla facilisis at vero eros.</p></div>
    <div class="img-fill about-photo" role="img" aria-label="Businessman in a dark suit holding a glowing tablet"></div>
    <footer class="slide-footer">www.boldledger.com | Page 1</footer>
  </section>

  <!-- Page 4 -->
  <div class="page-label c4 l1">Page 4</div>
  <section class="slide c4 r1">
    <header class="slide-header"><h2 class="slide-title">About our company</h2><div class="brand"><span class="brand-dot"></span><span class="brand-name">Bold Ledger</span></div></header>
    <div class="img-fill device-illustration" role="img" aria-label="Illustration of a laptop with colourful app icons bursting from the screen"></div>
    <div class="about4-text"><p class="body-text">Duis autem vel eum iriure dolor in hendrerit in vulputate velit esse molestie consequat, vel illum dolore eu feugiat nulla facilisis at vero eros.</p></div>
    <ul class="bullet-list">
      <li>Souvlaki ignitus carborundum e pluribus unum.</li>
      <li>Defacto lingo est igpay atinlay. Marquee selectus non provisio.</li>
      <li>Quote meon an estimate et non interruptus stadium.</li>
      <li>Sic tempus fugit esperanto hiccup estrogen.</li>
      <li>Epsum factorial non deposit quid pro quo hic escorol.</li>
    </ul>
    <footer class="slide-footer">www.boldledger.com | Page 2</footer>
  </section>

  <!-- Page 5 -->
  <div class="page-label c1 l2">Page 5</div>
  <section class="slide c1 r2">
    <header class="slide-header"><h2 class="slide-title">Title goes here</h2><div class="brand"><span class="brand-dot"></span><span class="brand-name">Bold Ledger</span></div></header>
    <div class="feature" style="left:12px">
      <svg width="36" height="28" viewBox="0 0 36 28" aria-hidden="true">
        <rect x="3" y="1" width="30" height="20" fill="none" stroke="#262b35" stroke-width="2"/>
        <rect x="6" y="4" width="24" height="14" fill="none" stroke="#262b35" stroke-width="1"/>
        <polyline points="8,15 13,10 17,13 23,7 28,9" fill="none" stroke="#262b35" stroke-width="1.3"/>
        <rect x="0" y="23" width="36" height="3" fill="#262b35"/>
      </svg>
      <p class="body-text">Duis autem vel eum iriure dolor in hendrerit in vulputate velit esse molestie consequat, vel illum dolore eu feugiat nulla facilisis at vero eros.</p>
    </div>
    <div class="feature" style="left:91px">
      <svg width="40" height="28" viewBox="0 0 40 28" aria-hidden="true">
        <g fill="none" stroke="#f78f20" stroke-width="2" stroke-linejoin="round" stroke-linecap="round">
          <path d="M2 9 L9 3 L14 8 L7 15 Z"/>
          <path d="M38 9 L31 3 L26 8 L33 15 Z"/>
          <path d="M13 7 L20 5 L28 9 L30 13 L21 24 L17 22 L10 15"/>
          <path d="M20 9 L16 13 L20 15 L24 12"/>
          <path d="M15 18 L18 21 M18 15 L22 19"/>
        </g>
      </svg>
      <p class="body-text">Duis autem vel eum iriure dolor in hendrerit in vulputate velit esse molestie consequat, vel illum dolore eu feugiat nulla facilisis at vero eros.</p>
    </div>
    <div class="feature" style="left:170px">
      <svg width="32" height="28" viewBox="0 0 32 28" aria-hidden="true">
        <g fill="none" stroke="#262b35" stroke-width="1.8" stroke-linejoin="round">
          <rect x="2" y="12" width="7" height="14"/>
          <path d="M9 13 L15 6 L16 1 C19 1 20 4 19 9 L28 9 C30 9 31 11 30 13 L27 24 C26 26 25 26 23 26 L9 26"/>
        </g>
      </svg>
      <p class="body-text">Duis autem vel eum iriure dolor in hendrerit in vulputate velit esse molestie consequat, vel illum dolore eu feugiat nulla facilisis at vero eros.</p>
    </div>
    <footer class="slide-footer">www.boldledger.com | Page 3</footer>
  </section>

  <!-- Page 6 -->
  <div class="page-label c2 l2">Page 6</div>
  <section class="slide c2 r2">
    <header class="slide-header"><h2 class="slide-title">Title goes here</h2><div class="brand"><span class="brand-dot"></span><span class="brand-name">Bold Ledger</span></div></header>
    <svg class="chart" width="232" height="92" viewBox="0 0 232 92" aria-label="Bar chart of three series across three categories">
      <g font-size="4" fill="#888" font-family="Lato,sans-serif">
        <text x="8" y="12">5</text><text x="8" y="24">4</text><text x="8" y="36">3</text><text x="8" y="48">2</text><text x="8" y="60">1</text><text x="8" y="72">0</text>
        <text x="40" y="82">Category 1</text><text x="109" y="82">Category 2</text><text x="180" y="82">Category 3</text>
      </g>
      <line x1="16" y1="71" x2="212" y2="71" stroke="#ccc" stroke-width=".5"/>
      <g>
        <rect x="33" y="20" width="12" height="51" fill="#f78f20"/><rect x="45" y="41" width="12" height="30" fill="#262b35"/><rect x="57" y="23" width="12" height="48" fill="#757575"/>
        <rect x="103" y="41" width="12" height="30" fill="#f78f20"/><rect x="115" y="19" width="12" height="52" fill="#262b35"/><rect x="127" y="29" width="12" height="42" fill="#757575"/>
        <rect x="172" y="35" width="12" height="36" fill="#f78f20"/><rect x="184" y="23" width="12" height="48" fill="#262b35"/><rect x="196" y="17" width="12" height="54" fill="#757575"/>
      </g>
      <line x1="216" y1="2" x2="216" y2="20" stroke="#ddd" stroke-width=".5"/>
      <g font-size="4" fill="#555" font-family="Lato,sans-serif">
        <rect x="218" y="4" width="2.5" height="2.5" fill="#f78f20"/><text x="222" y="6.6">Series 1</text>
        <rect x="218" y="10" width="2.5" height="2.5" fill="#262b35"/><text x="222" y="12.6">Series 2</text>
        <rect x="218" y="16" width="2.5" height="2.5" fill="#757575"/><text x="222" y="18.6">Series 3</text>
      </g>
    </svg>
    <p class="body-text chart-text">Duis autem vel eum iriure dolor in hendrerit in vulputate velit esse molestie consequat, vel illum dolore eu feugiat nulla facilisis at vero eros. Nam liber tempor cum soluta nobis eleifend option congue nihil imperdiet doming.</p>
    <footer class="slide-footer">www.boldledger.com | Page 4</footer>
  </section>

  <!-- Page 7 -->
  <div class="page-label c3 l2">Page 7</div>
  <section class="slide c3 r2">
    <header class="slide-header"><h2 class="slide-title">Title goes here</h2><div class="brand"><span class="brand-dot"></span><span class="brand-name">Bold Ledger</span></div></header>
    <svg class="chart" width="232" height="92" viewBox="0 0 232 92" aria-label="Area chart of three series across three categories">
      <g font-size="4" fill="#888" font-family="Lato,sans-serif">
        <text x="8" y="12">5</text><text x="8" y="24">4</text><text x="8" y="36">3</text><text x="8" y="48">2</text><text x="8" y="60">1</text><text x="8" y="72">0</text>
        <text x="14" y="82">Category 1</text><text x="92" y="82">Category 2</text><text x="174" y="82">Category 3</text>
      </g>
      <polygon points="92,33 210,19 210,40 92,48" fill="#262b35"/>
      <polygon points="16,47 58,26 92,30 140,33 16,60" fill="#f78f20"/>
      <polygon points="16,49 92,40 210,36 210,71 16,71" fill="#bdbdbd"/>
      <line x1="16" y1="71" x2="212" y2="71" stroke="#ccc" stroke-width=".5"/>
      <line x1="216" y1="2" x2="216" y2="20" stroke="#ddd" stroke-width=".5"/>
      <g font-size="4" fill="#555" font-family="Lato,sans-serif">
        <rect x="218" y="4" width="2.5" height="2.5" fill="#757575"/><text x="222" y="6.6">Series 1</text>
        <rect x="218" y="10" width="2.5" height="2.5" fill="#f78f20"/><text x="222" y="12.6">Series 2</text>
        <rect x="218" y="16" width="2.5" height="2.5" fill="#262b35"/><text x="222" y="18.6">Series 3</text>
      </g>
    </svg>
    <p class="body-text chart-text">Duis autem vel eum iriure dolor in hendrerit in vulputate velit esse molestie consequat, vel illum dolore eu feugiat nulla facilisis at vero eros. Nam liber tempor cum soluta nobis eleifend option congue nihil imperdiet doming.</p>
    <footer class="slide-footer">www.boldledger.com | Page 5</footer>
  </section>

  <!-- Page 8 -->
  <div class="page-label c4 l2">Page 8</div>
  <section class="slide c4 r2">
    <header class="slide-header"><h2 class="slide-title">Title goes here</h2><div class="brand"><span class="brand-dot"></span><span class="brand-name">Bold Ledger</span></div></header>
    <svg class="donut" width="62" height="62" viewBox="-31 -31 62 62" aria-label="Donut chart split into four equal quarters">
      <path d="M0,-30 A30,30 0 0,1 30,0 L11,0 A11,11 0 0,0 0,-11 Z" fill="#f78f20"/>
      <path d="M30,0 A30,30 0 0,1 0,30 L0,11 A11,11 0 0,0 11,0 Z" fill="#d3d3d3"/>
      <path d="M0,30 A30,30 0 0,1 -30,0 L-11,0 A11,11 0 0,0 0,11 Z" fill="#262b35"/>
      <path d="M-30,0 A30,30 0 0,1 0,-30 L0,-11 A11,11 0 0,0 -11,0 Z" fill="#3a3f48"/>
      <line x1="-31" y1="0" x2="31" y2="0" stroke="#fff" stroke-width="1.2"/>
      <line x1="0" y1="-31" x2="0" y2="31" stroke="#fff" stroke-width="1.2"/>
      <g font-size="5" fill="#fff" font-family="Lato,sans-serif" text-anchor="middle">
        <text x="-16" y="-7">25%</text><text x="16" y="-7">25%</text><text x="-16" y="11">25%</text><text x="16" y="11">25%</text>
      </g>
    </svg>
    <div class="donut-link" style="left:70px;top:48px;width:30px"></div>
    <div class="donut-link" style="left:146px;top:48px;width:30px"></div>
    <div class="donut-link" style="left:70px;top:115px;width:30px"></div>
    <div class="donut-link" style="left:146px;top:115px;width:30px"></div>
    <div class="donut-note" style="left:14px;top:41px"><h4>NOBIS VIDENTUR</h4><p class="body-text">Lorem ipsum dolor sit amet, consectetuer adipi scing elit, sed diam nonummy nibh euismod tin.</p></div>
    <div class="donut-note note-orange" style="left:166px;top:41px"><h4>NOBIS VIDENTUR</h4><p class="body-text">Lorem ipsum dolor sit amet, consectetuer adipi scing elit, sed diam nonummy nibh euismod tin.</p></div>
    <div class="donut-note" style="left:14px;top:108px"><h4>NOBIS VIDENTUR</h4><p class="body-text">Lorem ipsum dolor sit amet, consectetuer adipi scing elit, sed diam nonummy nibh euismod tin.</p></div>
    <div class="donut-note note-muted" style="left:170px;top:108px"><h4>NOBIS VIDENTUR</h4><p class="body-text">Lorem ipsum dolor sit amet, consectetuer adipi scing elit, sed diam nonummy nibh euismod tin.</p></div>
    <footer class="slide-footer">www.boldledger.com | Page 6</footer>
  </section>

  <!-- Page 9 -->
  <div class="page-label c1 l3">Page 9</div>
  <section class="slide c1 r3">
    <header class="slide-header"><h2 class="slide-title">Title goes here</h2><div class="brand"><span class="brand-dot"></span><span class="brand-name">Bold Ledger</span></div></header>
    <table class="data-table">
      <thead><tr><th></th><th>A</th><th>B</th><th>C</th></tr></thead>
      <tbody>
        <tr class="row-accent"><td class="row-name">Type 1</td><td>20</td><td>30</td><td>40</td></tr>
        <tr><td class="row-name">Type 2</td><td>50</td><td>60</td><td>70</td></tr>
        <tr class="row-accent"><td class="row-name">Type 3</td><td>80</td><td>90</td><td>100</td></tr>
      </tbody>
    </table>
    <footer class="slide-footer">www.boldledger.com | Page 7</footer>
  </section>

  <!-- Page 10 -->
  <div class="page-label c2 l3">Page 10</div>
  <section class="slide c2 r3">
    <header class="slide-header"><h2 class="slide-title">Title goes here</h2><div class="brand"><span class="brand-dot"></span><span class="brand-name">Bold Ledger</span></div></header>
    <div class="member" style="left:11px;top:50px">
      <div class="member-photo" role="img" aria-label="Portrait photo of team member A"></div>
      <div class="member-info"><p class="member-name">Mr A. Smith</p><p class="member-role">(President)</p><p class="body-text">Lorem ipsum dolor sit amet, consectetuer adipiscing elit, sed diam nonummy nibh euismod tincidunt ut laoreet dolore magna.</p></div>
    </div>
    <div class="member" style="left:130px;top:50px">
      <div class="member-photo" role="img" aria-label="Portrait photo of team member C"></div>
      <div class="member-info"><p class="member-name">Mr C. Smith</p><p class="member-role">(President)</p><p class="body-text">Lorem ipsum dolor sit amet, consectetuer adipiscing elit, sed diam nonummy nibh euismod tincidunt ut laoreet dolore magna.</p></div>
    </div>
    <div class="member" style="left:11px;top:112px">
      <div class="member-photo" role="img" aria-label="Portrait photo of team member B"></div>
      <div class="member-info"><p class="member-name">Mr B. Smith</p><p class="member-role">(President)</p><p class="body-text">Lorem ipsum dolor sit amet, consectetuer adipiscing elit, sed diam nonummy nibh euismod tincidunt ut laoreet dolore magna.</p></div>
    </div>
    <div class="member" style="left:130px;top:112px">
      <div class="member-photo" role="img" aria-label="Portrait photo of team member D"></div>
      <div class="member-info"><p class="member-name">Mr D. Smith</p><p class="member-role">(President)</p><p class="body-text">Lorem ipsum dolor sit amet, consectetuer adipiscing elit, sed diam nonummy nibh euismod tincidunt ut laoreet dolore magna.</p></div>
    </div>
    <footer class="slide-footer">www.boldledger.com | Page 8</footer>
  </section>

  <!-- Page 11 -->
  <div class="page-label c3 l3">Page 11</div>
  <section class="slide c3 r3">
    <header class="slide-header"><h2 class="slide-title">Title goes here</h2><div class="brand"><span class="brand-dot"></span><span class="brand-name">Bold Ledger</span></div></header>
    <div class="stat stat-orange" style="left:12px;top:43px">
      <svg width="22" height="18" viewBox="0 0 22 18" aria-hidden="true"><g fill="none" stroke="#fff" stroke-width="1.4" stroke-linejoin="round"><path d="M2 6 H7 L15 1 V15 L7 10 H2 Z"/><path d="M5 10 L7 16 H9 L8 10"/><path d="M17 5 L20 3 M17 8 H21 M17 11 L20 13"/></g></svg>
      <p class="stat-value">915,456,459</p>
      <p class="stat-text">Lorem ipsum dolor sit amet, consectetuer adipiscing elit, sed diam nonu mmy nibh euis mod tincidunt</p>
    </div>
    <div class="stat stat-grey" style="left:130px;top:43px">
      <svg width="22" height="20" viewBox="0 0 22 20" aria-hidden="true"><g fill="none" stroke="#fff" stroke-width="1.4"><path d="M8 5 L6 1 H16 L14 5 C19 8 20 13 19 16 C18 19 4 19 3 16 C2 13 3 8 8 5 Z"/><path d="M13 9 C12 8 9 8 9 10 C9 12 13 11 13 13 C13 15 10 15 9 14 M11 7 V16"/></g></svg>
      <p class="stat-value">111,458,564</p>
      <p class="stat-text">Lorem ipsum dolor sit amet, consectetuer adipiscing elit, sed diam nonu mmy nibh euis mod tincidunt</p>
    </div>
    <div class="stat stat-navy" style="left:12px;top:102px">
      <svg width="22" height="18" viewBox="0 0 22 18" aria-hidden="true"><g fill="#fff"><ellipse cx="11" cy="10" rx="8" ry="6"/><rect x="6" y="14" width="2.5" height="3"/><rect x="13" y="14" width="2.5" height="3"/><rect x="18" y="8" width="3" height="3"/><circle cx="12" cy="2.5" r="2"/></g></svg>
      <p class="stat-value">100%</p>
      <p class="stat-text">Lorem ipsum dolor sit amet, consectetuer adipiscing elit, sed diam nonu mmy nibh euis mod tincidunt</p>
    </div>
    <div class="stat stat-dark" style="left:130px;top:102px">
      <svg width="22" height="18" viewBox="0 0 22 18" aria-hidden="true"><g fill="none" stroke="#fff" stroke-width="1.3"><rect x="3" y="11" width="4" height="6"/><rect x="9" y="7" width="4" height="10"/><rect x="15" y="2" width="4" height="15"/><line x1="1" y1="17" x2="21" y2="17"/></g></svg>
      <p class="stat-value">100%</p>
      <p class="stat-text">Lorem ipsum dolor sit amet, consectetuer adipiscing elit, sed diam nonu mmy nibh euis mod tincidunt</p>
    </div>
    <footer class="slide-footer">www.boldledger.com | Page 9</footer>
  </section>

  <!-- Page 12 -->
  <div class="page-label c4 l3">Page 12</div>
  <section class="slide c4 r3">
    <div class="closing-top"></div>
    <div class="closing-brand"><span class="brand-dot"></span><span class="brand-name">Bold Ledger</span></div>
    <h2 class="closing-title">THANK YOU</h2>
    <p class="closing-url">www.boldledger.com</p>
  </section>
</div>
</body>
</html>
```